Biz Card

MARKETING today is the most rapidly changing business discipline. Media options to reach customers, actual customer preferences and consumer buying decisions change by the minute . . . no, by the second. The behavioral data generated by all aspects of the business and the new technologies that put the data to work together produce the potential to generate business intelligence and guide smart resource allocation to influence purchase and retention. However, to realize this potential, marketing professionals at all levels and in all organizations must continuously improve their skills not just from on-the-job training but by learning from masters in the field. The Bright Horizon Guild is the training center that serves this professional development need.model logos:msi.orgama.orgcontentmarketinginstitute.comBook covers on MarketingMetrics, Marketing Anaytics
Industry/Entity Type
Business
Contact Information for Business Card
Roy A. YoungCEOMarketing Science Academyphone: 310-601-4755email: roy@marketingscience.comAddress:437 South Rexford DriveBeverly Hills, CA 89377
Look and feel
Each slider illustrates characteristics of the customer's brand and the style your logo design should communicate.

```html
<!DOCTYPE html>
<html lang="en">
<head>
<meta charset="utf-8">
<title>Bright Horizon Guild – Business Card</title>
<link rel="stylesheet" href="https://fonts.googleapis.com/css2?family=Roboto:wght@400;500;700&display=swap">
<style>
  :root {
    --backdrop: #a8a6a6;
    --paper: #ffffff;
    --brand-red: #8e2624;
    --brand-grey: #545353;
    --text-grey: #4a4a4a;
    --rule-grey: #565555;
  }
  * { margin: 0; padding: 0; box-sizing: border-box; }
  html, body { width: 1200px; height: 1200px; overflow: hidden; }
  body {
    background: var(--backdrop);
    font-family: "Roboto", Arial, sans-serif;
    position: relative;
  }
  .card {
    position: absolute;
    width: 713px;
    height: 418px;
    background: var(--paper);
    overflow: hidden;
  }
  .card--front { left: 238px; top: 119px; }
  .card--back { left: 230px; top: 645px; }

  .front-band {
    position: absolute;
    left: 0; right: 0; bottom: 0;
    height: 16px;
    background: var(--brand-red);
  }

  .brand {
    position: absolute;
    display: flex;
    align-items: center;
    gap: 24px;
  }
  .brand__dot {
    width: 70px; height: 70px;
    border-radius: 50%;
    background: var(--brand-red);
    flex: none;
  }
  .brand__name {
    font-weight: 700;
    font-size: 32px;
    line-height: 32px;
    letter-spacing: 0.5px;
    text-transform: uppercase;
    color: var(--brand-grey);
  }
  .card--front .brand { left: 140px; top: 162px; }
  .card--back .brand { left: 42px; top: 60px; }

  .address {
    position: absolute;
    left: 43px; top: 205px;
    font-size: 16.5px;
    color: var(--text-grey);
  }
  .contact-list {
    position: absolute;
    left: 43px; top: 244px;
    list-style: none;
  }
  .contact-list li {
    display: flex;
    align-items: center;
    gap: 19px;
    height: 24px;
    font-size: 16.5px;
    color: var(--text-grey);
  }
  .contact-list svg { width: 16px; height: 14px; flex: none; fill: var(--brand-red); }

  .back-rule {
    position: absolute;
    left: 0; right: 0;
    top: 326px;
    height: 4px;
    background: var(--rule-grey);
  }
  .back-band {
    position: absolute;
    left: 0; right: 0; bottom: 0;
    height: 82px;
    background: var(--brand-red);
  }

  .person {
    position: absolute;
    right: 42px;
    top: 346px;
    text-align: right;
    color: #ffffff;
  }
  .person__name { font-weight: 500; font-size: 25px; line-height: 30px; }
  .person__role { font-size: 14px; margin-top: 6px; letter-spacing: 0.5px; }
</style>
</head>
<body>

<section class="card card--front" aria-label="Business card front">
  <div class="brand">
    <span class="brand__dot"></span>
    <span class="brand__name">Bright<br>Horizon<br>Guild</span>
  </div>
  <div class="front-band"></div>
</section>

<section class="card card--back" aria-label="Business card back">
  <div class="brand">
    <span class="brand__dot"></span>
    <span class="brand__name">Bright<br>Horizon<br>Guild</span>
  </div>

  <p class="address">912 North Calloway Lane Beverly Hills, CA 89377</p>

  <ul class="contact-list">
    <li>
      <svg viewBox="0 0 16 14" aria-hidden="true"><path d="M1 4 C1 1 15 1 15 4 L12 5 L11 3.5 L5 3.5 L4 5 Z M3 6 L13 6 L14 13 L2 13 Z"/></svg>
      310-555-0182
    </li>
    <li>
      <svg viewBox="0 0 16 14" aria-hidden="true"><path d="M1 2 L15 2 L15 12 L1 12 Z M2 3 L8 8 L14 3 Z" fill-rule="evenodd"/></svg>
      neil@brighthorizonguild.com
    </li>
    <li>
      <svg viewBox="0 0 16 14" aria-hidden="true"><circle cx="8" cy="7" r="6.5"/><path d="M1.5 7 H14.5 M8 0.5 V13.5 M3 3.5 H13 M3 10.5 H13" stroke="#fff" stroke-width="1" fill="none"/></svg>
      www.brighthorizonguild.com
    </li>
  </ul>

  <div class="back-rule"></div>
  <div class="back-band"></div>

  <div class="person">
    <p class="person__name">Neil P. Barton</p>
    <p class="person__role">CEO</p>
  </div>
</section>

</body>
</html>
```